Tandem Hearth Works Pty Ltd

We need business cards for a company based in Perth, we install, service and maintain fire equipment.
On the front we want a great design with our logo and a small spot for our full company name, general company email address and office number. On the back we need space for our name, title, mobile number and email address on the back.

Target Market(s)

Facility managers and commercial/industrial building owners/occupiers.

Contact Information for Business Card

Font styles to use
Sans Serif

Requirements
Must have
• Please only submit 5 of your best samples.
Darker tones are preferred.
Nice to have
• We want to use, black, red and grey. Keep it modern and clean.
I've attached the company logo and a sample of a boarder we use on our emergency plans.
Should not have
• No preference. Let the designer choose.

```html
<!DOCTYPE html>
<html lang="en">
<head>
<meta charset="utf-8">
<title>Tandem Hearth Works – Business Card</title>
<link rel="stylesheet" href="https://fonts.googleapis.com/css2?family=Montserrat:wght@400;700;800&family=Roboto:wght@300;400&display=swap">
<style>
  :root {
    --bg: #3a3a3d;
    --card-front: #2a2a2c;
    --card-back: #0f0f10;
    --red: #ee1c25;
    --white: #f2f2f2;
    --emboss: #1f1f21;
    --muted: #55555a;
  }
  * { margin: 0; padding: 0; box-sizing: border-box; }
  html, body { width: 1200px; height: 1200px; overflow: hidden; }
  body {
    background: var(--bg);
    font-family: "Roboto", sans-serif;
    display: flex; flex-direction: column; align-items: center; justify-content: center;
    gap: 50px;
  }
  .card {
    position: relative;
    width: 880px; height: 503px;
    border-radius: 28px;
    box-shadow: 0 18px 40px rgba(0,0,0,.45);
    overflow: hidden;
  }
  /* front face */
  .card--front { background: var(--card-front); }
  .brand-mark {
    position: absolute; left: 0; right: 0; top: 150px;
    text-align: center;
    font-family: "Montserrat", sans-serif; font-weight: 800;
    font-size: 56px; letter-spacing: 2px; line-height: 1.1;
    color: var(--emboss);
  }
  .front-details {
    position: absolute; left: 0; right: 0; top: 370px;
    text-align: center; color: var(--muted);
    font-size: 20px; font-weight: 300; line-height: 1.5;
  }
  .front-details .dot {
    display: inline-block; width: 7px; height: 7px; border-radius: 50%;
    background: var(--red); vertical-align: middle; margin: 0 8px 4px;
  }
  /* back face */
  .card--back {
    background: radial-gradient(ellipse at 45% 30%, #1c1c1d 0%, var(--card-back) 70%);
  }
  .back-brand {
    position: absolute; right: 70px; top: 95px; width: 330px;
    text-align: right;
    font-family: "Montserrat", sans-serif; font-weight: 800;
    font-size: 50px; line-height: 1.05; color: var(--red);
  }
  .person { position: absolute; left: 70px; top: 215px; }
  .person__name {
    font-family: "Montserrat", sans-serif; font-weight: 700;
    font-size: 28px; letter-spacing: 5px; color: var(--red);
  }
  .person__title {
    margin-top: 4px; font-size: 16px; letter-spacing: 4px; color: var(--white);
  }
  .divider {
    position: absolute; left: 200px; right: 90px; top: 300px;
    height: 2px; background: var(--red);
  }
  .contacts {
    position: absolute; left: 470px; top: 340px;
    list-style: none; color: var(--white);
    font-size: 21px; letter-spacing: 2px;
  }
  .contacts li { display: flex; align-items: center; gap: 16px; height: 38px; }
  .contacts svg { width: 18px; height: 18px; fill: none; stroke: var(--red); stroke-width: 2; }
</style>
</head>
<body>
  <section class="card card--front">
    <div class="brand-mark">TANDEM<br>HEARTH WORKS</div>
    <div class="front-details">
      <div><span class="dot"></span>Your FullCompanyName<span class="dot"></span></div>
      <div>123 456 7890 | youremail.com</div>
    </div>
  </section>

  <section class="card card--back">
    <div class="back-brand">TANDEM HEARTH WORKS</div>
    <div class="person">
      <div class="person__name">MARCUS HALE</div>
      <div class="person__title">FOUNDER &amp; CEO</div>
    </div>
    <div class="divider"></div>
    <ul class="contacts">
      <li>
        <svg viewBox="0 0 24 24"><path d="M5 3h4l2 5-2.5 1.5a11 11 0 0 0 6 6L16 13l5 2v4a2 2 0 0 1-2 2A17 17 0 0 1 3 5a2 2 0 0 1 2-2z"/></svg>
        +61 400 555 013
      </li>
      <li>
        <svg viewBox="0 0 24 24"><rect x="2" y="5" width="20" height="14" rx="1"/><path d="M2 6l10 7 10-7"/></svg>
        ceo@tandemhearth.com
      </li>
      <li>
        <svg viewBox="0 0 24 24"><circle cx="12" cy="12" r="10"/><path d="M2 12h20M12 2a15 15 0 0 1 0 20M12 2a15 15 0 0 0 0 20"/></svg>
        www.tandemhearth.com
      </li>
    </ul>
  </section>
</body>
</html>
```